Redesign of the UI of a customer service platform

To improve the user experience of our customers, we need a new design for our agent interface of our customer service platform (velorant.com).
The focus will be on the dashboard and the inbox screens (see attached) along with the common UI elements (Buttons, menu, fonts, forms...)
We want a simple and distinctive design

Target Market(s)

Worldwide

Industry/Entity Type

It Service

Number of Pages Required

3 page

Font styles to use
Sans Serif

Requirements
Must have
• New Onboarding page: this is a new page that is shown to user the first time they login to the platform. This will replace the current onboarding screen (setup SMS, Setup widget...etc)
• Dashboard page: to access important information and activate services (see screenshot from current site)
• Inbox page: to manage all the interactions with customers. (see screenshot from current site)
• UI elements (buttons, menus, forms, tables, fonts, color palette)

```html
<!DOCTYPE html>
<html lang="en">
<head>
<meta charset="utf-8">
<title>velorant — Dashboard</title>
<link href="https://fonts.googleapis.com/css2?family=Roboto:wght@400;500&display=swap" rel="stylesheet">
<style>
:root{
  --bg:#eceef2;--dark:#222;--dark2:#2b2b2b;--red:#e3262a;--red2:#ef4f4f;
  --green:#0aa50a;--blue:#0a63f5;--orange:#ffa500;--sky:#56b6e2;--ink:#333;--muted:#555;
  --soft:#d6ecf8;--line:#d9d9d9;
}
*{box-sizing:border-box;margin:0;padding:0}
html,body{width:1200px;height:903px;overflow:hidden}
body{font-family:'Roboto',sans-serif;background:var(--bg);color:var(--ink);position:relative}
.abs{position:absolute}
.header{left:0;top:0;width:1200px;height:89px;background:#fff}
.brand{left:24px;top:24px;display:flex;align-items:center;gap:6px;font-size:31px;font-weight:500;color:#333}
.brand .dot{width:26px;height:26px;border-radius:50%;background:#333}
.hdr-icon{top:31px;width:22px;height:22px}
.badge{left:740px;top:23px;width:23px;height:16px;border-radius:8px;background:#e74c3c;color:#fff;font-size:11px;text-align:center;line-height:16px}
.status{left:834px;top:37px;font-size:15px;color:#555;display:flex;align-items:center;gap:6px}
.status i{width:10px;height:10px;border-radius:50%;background:#5cb85c;display:block}
.avatar{left:940px;top:23px;width:43px;height:44px;background:linear-gradient(160deg,#c9a27f,#6e4a34)}
.welcome{left:995px;top:36px;font-size:15px;color:#555}
.help{left:1148px;top:34px;width:19px;height:19px;border-radius:50%;background:#555;color:#fff;font-size:13px;font-weight:500;text-align:center;line-height:19px}
.sidebar{left:0;top:89px;width:209px;height:736px;background:var(--dark)}
.nav{list-style:none}
.nav li{height:56px;display:flex;align-items:center;border-bottom:1px solid #1a1a1a;color:#fff;font-size:19px}
.nav .ic{width:69px;height:100%;background:var(--dark2);display:flex;align-items:center;justify-content:center}
.nav .lbl{flex:1;padding-left:14px;display:flex;justify-content:space-between;padding-right:22px}
.nav li.active .ic{background:var(--red)}
.nav li.active .lbl{background:var(--red2);height:100%;align-items:center}
.feedback{left:0;top:771px;width:209px;height:54px;background:#2e2e2e;color:#fff;font-size:19px;display:flex;align-items:center;gap:14px;padding-left:24px}
.footer{left:0;top:825px;width:1200px;height:78px;background:var(--dark);color:#fff;font-size:12.5px;text-align:center;padding-top:36px}
.page-title{left:243px;top:110px;font-size:27px;color:#222;display:flex;align-items:center;gap:8px}
.stat{top:155px;width:204px;height:103px;color:#fff;padding:18px}
.stat .num{font-size:26px;display:flex;align-items:center;gap:12px}
.stat .cap{font-size:12px;line-height:14px;margin-top:6px}
.section-h{font-size:17px;color:#333}
.chart{left:244px;top:351px;width:401px;height:332px;background:#fff;box-shadow:0 1px 3px rgba(0,0,0,.2)}
.toggle{left:580px;top:343px;width:63px;height:28px;background:#f5f5f5;border:1px solid #ccc;display:flex}
.toggle span{flex:1;border-right:1px solid #ccc}
.side-btn{left:654px;width:40px;height:34px;border-radius:2px;display:flex;align-items:center;justify-content:center}
.card{left:716px;width:451px;background:var(--soft);border-left:4px solid var(--sky);box-shadow:0 1px 3px rgba(0,0,0,.15);padding:10px 17px}
.card h3{font-size:15px;font-weight:400;color:#222}
.card p{font-size:11px;color:#555;line-height:16px;margin-top:2px}
.btn{position:absolute;right:17px;background:var(--blue);color:#fff;font-size:11px;font-weight:500;padding:5px 8px;border-radius:2px}
.plan{top:334px;height:116px;background:#fff}
.addon{position:absolute;top:49px;height:50px;background:#f1f1f1;border:1px solid #e0e0e0;font-size:11px;color:#444;display:flex;align-items:center;gap:10px;padding-left:12px;line-height:15px}
.pill{position:absolute;top:-8px;right:-10px;width:22px;height:22px;border-radius:50%;background:var(--sky);color:#fff;font-size:10px;text-align:center;line-height:22px}
</style>
</head>
<body>
<header class="abs header">
  <div class="abs brand"><span class="dot"></span>velorant</div>
  <svg class="abs hdr-icon" style="left:741px" viewBox="0 0 22 22"><path d="M2 10h18v10H2z M5 3h12l3 7H2z" fill="#444"/><rect x="7" y="10" width="8" height="3" fill="#fff"/></svg>
  <div class="abs badge">8</div>
  <svg class="abs hdr-icon" style="left:791px" viewBox="0 0 22 22"><path d="M3 13l10-10 6 6-10 10z" fill="none" stroke="#444" stroke-width="2.5"/></svg>
  <div class="abs status"><i></i>Available ▾</div>
  <div class="abs avatar" role="img" aria-label="Agent profile photo"></div>
  <div class="abs welcome">Welcome, Marlo ▾</div>
  <div class="abs help">?</div>
</header>

<nav class="abs sidebar">
  <ul class="nav">
    <li class="active"><span class="ic"><svg width="18" height="16" viewBox="0 0 18 16"><path d="M9 1L1 8h2v7h4v-4h4v4h4V8h2z" fill="#fff"/></svg></span><span class="lbl">Dashboard<span>›</span></span></li>
    <li><span class="ic"><svg width="18" height="14" viewBox="0 0 18 14"><path d="M1 6h16v8H1zM4 0h10l3 6H1z" fill="#fff"/></svg></span><span class="lbl">Inbox<span>›</span></span></li>
    <li><span class="ic"><svg width="18" height="18" viewBox="0 0 18 18"><path d="M2 11l9-9 5 5-9 9z" fill="#fff"/></svg></span><span class="lbl">Tickets<span>›</span></span></li>
    <li><span class="ic"><svg width="22" height="16" viewBox="0 0 22 16"><circle cx="11" cy="4" r="3.5" fill="#fff"/><circle cx="4" cy="5" r="2.5" fill="#fff"/><circle cx="18" cy="5" r="2.5" fill="#fff"/><path d="M5 16c0-5 12-5 12 0zM0 13c0-4 6-4 6-1zM22 13c0-4-6-4-6-1z" fill="#fff"/></svg></span><span class="lbl">Clients<span>›</span></span></li>
    <li><span class="ic"><svg width="22" height="18" viewBox="0 0 22 18"><path d="M1 0v17h21" stroke="#fff" stroke-width="2" fill="none"/><path d="M5 9h2v6H5zM9 5h2v10H9zM13 8h2v7h-2zM17 3h2v12h-2z" fill="#fff"/></svg></span><span class="lbl">Reports<span>›</span></span></li>
    <li><span class="ic"><svg width="22" height="18" viewBox="0 0 22 18"><circle cx="8" cy="10" r="6" fill="none" stroke="#fff" stroke-width="3" stroke-dasharray="3 2"/><circle cx="17" cy="5" r="3.5" fill="none" stroke="#fff" stroke-width="2.2"/></svg></span><span class="lbl">Settings<span>›</span></span></li>
  </ul>
</nav>
<div class="abs feedback"><svg width="20" height="15" viewBox="0 0 20 15"><rect x="1" y="1" width="18" height="13" fill="none" stroke="#fff" stroke-width="1.6"/><path d="M1 1l9 7 9-7" fill="none" stroke="#fff" stroke-width="1.6"/></svg>Send Feedback</div>

<main>
  <h1 class="abs page-title" style="font-weight:400"><svg width="20" height="18" viewBox="0 0 18 16"><path d="M9 1L1 8h2v7h4v-4h4v4h4V8h2z" fill="#222"/></svg>Dashboard</h1>

  <div class="abs stat" style="left:243px;background:var(--green)"><div class="num"><svg width="38" height="38" viewBox="0 0 20 20"><circle cx="10" cy="6" r="5" fill="#fff"/><path d="M1 20c0-8 18-8 18 0z" fill="#fff"/></svg>0/0</div><div class="cap">TOTAL CLIENTS<br>SERVED/NON-SERVED</div></div>
  <div class="abs stat" style="left:483px;background:var(--blue)"><div class="num"><svg width="42" height="42" viewBox="0 0 22 22"><path d="M2 12l10-10 8 8-10 10z" fill="none" stroke="#fff" stroke-width="2.5"/></svg>0/0</div><div class="cap">CLIENT TICKETS<br>CLOSED/OPENED</div></div>
  <div class="abs stat" style="left:722px;background:var(--orange)"><div class="num"><svg width="48" height="36" viewBox="0 0 24 18"><ellipse cx="10" cy="7" rx="9" ry="6" fill="#fff"/><ellipse cx="16" cy="11" rx="7" ry="5" fill="#fff" stroke="var(--orange)" stroke-width="1"/></svg>0</div><div class="cap" style="margin-top:12px">TOTAL CHAT MESSAGES</div></div>
  <div class="abs stat" style="left:962px;background:var(--sky)"><div class="num"><svg width="48" height="36" viewBox="0 0 24 18"><ellipse cx="10" cy="7" rx="8.5" ry="5.5" fill="none" stroke="#fff" stroke-width="1.8"/><path d="M15 12.5c3 0 7-1 7-4" fill="none" stroke="#fff" stroke-width="1.8"/></svg>0</div><div class="cap" style="margin-top:12px">TOTAL SMS MESSAGES</div></div>

  <h2 class="abs section-h" style="left:244px;top:298px;font-weight:400">Reports</h2>
  <section class="abs chart">
    <svg width="401" height="332" viewBox="0 0 401 332">
      <text x="200" y="57" text-anchor="middle" font-size="14.5" fill="#333">Clients total: served vs non-served (Account)</text>
      <text x="200" y="77" text-anchor="middle" font-size="11.5" fill="#444">from 23 December 2016 to 07 january 2017</text>
      <g stroke="#e3e3e3"><line x1="39" y1="105" x2="377" y2="105"/><line x1="39" y1="147" x2="377" y2="147"/><line x1="39" y1="190" x2="377" y2="190"/><line x1="39" y1="232" x2="377" y2="232"/><line x1="39" y1="105" x2="39" y2="275"/><line x1="377" y1="105" x2="377" y2="275"/></g>
      <line x1="39" y1="275" x2="377" y2="275" stroke="#999"/>
      <g font-size="12" fill="#555" text-anchor="end"><text x="30" y="109">4</text><text x="30" y="151">3</text><text x="30" y="194">2</text><text x="30" y="236">1</text></g>
      <rect x="70" y="228" width="23" height="47" fill="#a8e8d5"/>
      <rect x="122" y="211" width="23" height="64" fill="#62dcb8"/>
      <rect x="174" y="217" width="23" height="58" fill="#22c393"/>
      <rect x="226" y="177" width="23" height="98" fill="#1eb184"/>
      <rect x="281" y="147" width="23" height="128" fill="#18a276"/>
      <rect x="337" y="118" width="23" height="157" fill="#2e9a7a"/>
      <g font-size="10" fill="#555" text-anchor="middle"><text x="84" y="292">23 Dec</text><text x="136" y="292">24 Dec</text><text x="189" y="292">25 Dec</text><text x="241" y="292">26 Dec</text><text x="297" y="292">27 Dec</text><text x="353" y="292">28 Dec</text></g>
    </svg>
  </section>
  <div class="abs toggle"><span></span><span style="border:0"></span></div>
  <div class="abs side-btn" style="top:345px;background:var(--green)"><svg width="18" height="18" viewBox="0 0 20 20"><circle cx="10" cy="6" r="5" fill="#fff"/><path d="M1 20c0-8 18-8 18 0z" fill="#fff"/></svg></div>
  <div class="abs side-btn" style="top:392px;background:var(--blue)"><svg width="20" height="20" viewBox="0 0 22 22"><path d="M3 12l9-9 7 7-9 9z" fill="none" stroke="#fff" stroke-width="2.5"/></svg></div>
  <div class="abs side-btn" style="top:435px;background:var(--orange)"><svg width="22" height="16" viewBox="0 0 24 18"><ellipse cx="10" cy="7" rx="9" ry="6" fill="#fff"/><ellipse cx="16" cy="11" rx="7" ry="5" fill="#fff"/></svg></div>
  <div class="abs side-btn" style="top:478px;background:var(--sky)"><svg width="22" height="16" viewBox="0 0 24 18"><ellipse cx="10" cy="7" rx="8.5" ry="5.5" fill="none" stroke="#fff" stroke-width="2"/></svg></div>

  <h2 class="abs section-h" style="left:716px;top:294px;font-weight:400">Plan &amp; Add-ons</h2>
  <section class="abs card plan">
    <h3>Plan (Pro)</h3>
    <span class="btn" style="top:11px;background:var(--green)">✔ Upgrade</span>
    <div class="addon" style="left:17px;width:108px"><svg width="24" height="18" viewBox="0 0 22 16"><circle cx="11" cy="4" r="3.5" fill="#333"/><circle cx="4" cy="5" r="2.5" fill="#333"/><circle cx="18" cy="5" r="2.5" fill="#333"/><path d="M5 16c0-5 12-5 12 0zM0 13c0-4 6-4 6-1zM22 13c0-4-6-4-6-1z" fill="#333"/></svg><span>Agents<br>Unlimited</span><span class="pill">1/1</span></div>
    <div class="addon" style="left:142px;width:122px"><svg width="22" height="18" viewBox="0 0 22 18"><rect x="1" y="4" width="20" height="13" rx="2" fill="#333"/><rect x="7" y="1" width="8" height="4" fill="none" stroke="#333" stroke-width="1.6"/></svg><span>Departments<br>Unlimited</span><span class="pill">1</span></div>
    <div class="addon" style="left:283px;width:107px"><svg width="18" height="18" viewBox="0 0 18 18"><path d="M3 1l4 4-2 2c1 3 3 5 6 6l2-2 4 4-3 2C7 17 1 11 1 4z" fill="#333"/></svg><span style="padding-left:8px">Phones<br>Unlimited</span><span class="pill">0</span></div>
  </section>
  <section class="abs card" style="top:465px;height:78px">
    <h3>Phones + SMS</h3>
    <p>Allow clients to send SMS messages right to your inbox.<br>You may reply th mrwm SMS messages too</p>
    <span class="btn" style="top:29px">✔ Add phones</span>
  </section>
  <section class="abs card" style="top:557px;height:58px">
    <h3>Payvane</h3><p>Receive one time payments with Payvane</p>
    <span class="btn" style="top:19px">✔ Activate</span>
  </section>
  <section class="abs card" style="top:630px;height:58px">
    <h3>Wiregram</h3><p>Receive chat messages with Wiregram</p>
    <span class="btn" style="top:19px">✔ Activate</span>
  </section>
  <section class="abs card" style="top:703px;height:58px">
    <h3>Linkmesh Messenger</h3><p>Remove chat messages with Linkmesh Messenger</p>
    <span class="btn" style="top:19px">✔ Activate</span>
  </section>
</main>

<footer class="abs footer">Copyright © 2017. All Rights Reserved</footer>
</body>
</html>
```